QRV Advisors needs a web site

We need a web site for www.qrvadvisors-example.com. QRV is a mergers and acquisition consulting company that focuses our buyer and seller services on logistics companies. We help put companies together, and help with legal and financial due diligence. We want the web site to express our service and show the logistics components. We want personalized images versus pictures of trucks and airplanes.

Our new logo uses Burgandy and grey colors. Image attached. We are not in to bold, big letters...classy, artistic, low key preferred. Confidentiality, experience, professional are what we want to express on the site.

All we expect for the first part of this project is a home page, and one subpage.  We are budgeting other funds for the technical aspects of the web site

Reason: All that I'm seeing so far is trucks, forklifts and planes. We are a legal mergers and acquisitions firm that focus on logistics. I like some of the images to say logistics, but really want it say legal, financial, and putting companies together. Will pay extra for the sub page if someone can impress us with a home page.

Reason: Swamped with another project at the moment...will work on this over the weekend and provide designer feedback and select final design by Tuesday

```html
<!DOCTYPE html>
<html lang="en">
<head>
<meta charset="utf-8">
<title>QRV Advisors — Home</title>
<link rel="stylesheet" href="https://fonts.googleapis.com/css2?family=Open+Sans:wght@300;400;600;700&display=swap">
<style>
  :root {
    --burgundy: #a0002a;
    --burgundy-dark: #86001f;
    --rose: #9c2a48;
    --ink: #333333;
    --text: #555555;
    --muted: #888888;
    --navy: #2d3561;
    --hero-blue: #c8d2e6;
    --panel-dark: #2a2b2d;
    --footer: #2d2d2d;
    --white: #ffffff;
  }
  * { box-sizing: border-box; margin: 0; padding: 0; }
  html, body { width: 1200px; height: 1016px; overflow: hidden; background: var(--white); }
  body { position: relative; font-family: "Open Sans", Arial, sans-serif; color: var(--text); }
  .abs { position: absolute; white-space: nowrap; }

  /* header */
  .brand { left: 110px; top: 34px; font-size: 38px; font-weight: 600; color: var(--burgundy); letter-spacing: 0.3px; line-height: 1; }
  .questions { left: 866px; top: 22px; font-size: 12.5px; color: var(--muted); letter-spacing: 0.2px; }
  .contact-icons { left: 1028px; top: 17px; }
  .social-top { left: 932px; top: 62px; display: flex; gap: 7px; }
  .social-top span { width: 26px; height: 26px; border-radius: 50%; background: #111; display: block; }

  /* hero */
  .hero { left: 0; top: 125px; width: 1200px; height: 451px; background: var(--hero-blue); }
  .hero-photo { left: 470px; top: 125px; width: 730px; height: 451px;
    background: linear-gradient(100deg, #c8d2e6 0%, #d6dcea 35%, #b8c2d8 60%, #3a4050 80%, #1c2130 100%); }
  .nav { left: 110px; top: 123px; width: 980px; height: 50px; display: flex;
    background: linear-gradient(#a8042f, var(--burgundy-dark)); box-shadow: 0 2px 4px rgba(0,0,0,.25); }
  .nav a { color: var(--white); text-decoration: none; font-size: 13.5px; line-height: 50px; text-align: center;
    border-right: 1px solid rgba(0,0,0,.18); box-shadow: 1px 0 0 rgba(255,255,255,.08); white-space: nowrap; }
  .nav a:last-child { border-right: 0; box-shadow: none; }

  /* slide caption */
  .headline-1 { left: 110px; top: 274px; width: 280px; height: 42px; background: var(--panel-dark);
    color: var(--white); font-size: 23.5px; line-height: 42px; padding-left: 10px; }
  .headline-2 { left: 110px; top: 316px; width: 520px; height: 42px; background: var(--panel-dark);
    color: var(--white); font-size: 23.5px; line-height: 42px; padding-left: 16px; font-weight: 300; letter-spacing: -0.3px; }
  .headline-2 b { font-weight: 600; }
  .slide-lead { left: 110px; top: 358px; width: 502px; height: 44px; background: var(--rose);
    color: var(--white); font-size: 13.5px; line-height: 44px; padding-left: 13px; }
  .more-details { left: 110px; top: 410px; width: 111px; height: 38px; background: var(--white);
    border-bottom: 3px solid var(--burgundy); color: var(--burgundy); font-size: 12px; line-height: 36px; text-align: center; }
  .dots { left: 110px; top: 465px; display: flex; gap: 8px; align-items: center; }
  .dots i { width: 8px; height: 8px; border-radius: 50%; background: var(--burgundy); display: block; }
  .dots i.on { width: 11px; height: 11px; background: #222; }

  /* feature cards */
  .card { top: 513px; width: 299px; height: 112px; background: linear-gradient(#ffffff, #f1f3f7);
    border: 1px solid #e2e5ea; box-shadow: 0 1px 3px rgba(0,0,0,.12); }
  .card h3 { position: absolute; left: 11px; top: 23px; font-size: 18.5px; font-weight: 400; color: var(--navy); white-space: nowrap; }
  .card p { position: absolute; left: 12px; top: 56px; font-size: 12px; line-height: 16px; color: var(--muted); white-space: nowrap; }
  .card svg { position: absolute; }

  /* welcome */
  .welcome-title { left: 112px; top: 680px; font-size: 23px; font-weight: 400; color: var(--ink); }
  .welcome-copy { left: 111px; top: 722px; font-size: 13.2px; line-height: 27.5px; color: var(--text); }
  .btn { height: 30px; background: var(--burgundy); color: var(--white); font-size: 14px; line-height: 30px;
    text-align: center; width: 97px; }

  /* testimonials */
  .testi-title { left: 829px; top: 679px; font-size: 25px; font-weight: 300; color: var(--burgundy); }
  .avatar { width: 57px; height: 57px; background: linear-gradient(#d9d2c6, #a8a39a); }
  .quote { left: 896px; font-size: 12px; line-height: 18px; color: var(--text); }
  .quote-name { font-size: 13.5px; font-weight: 600; color: var(--burgundy); }

  /* footer */
  .footer { left: 0; top: 967px; width: 1200px; height: 49px; background: var(--footer); }
  .copyright { left: 108px; top: 983px; font-size: 12.5px; color: #9a9a9a; }
  .socialize { left: 864px; top: 983px; font-size: 12.5px; color: #9a9a9a; }
  .social-foot { left: 982px; top: 976px; display: flex; gap: 8px; }
  .social-foot span { width: 31px; height: 31px; display: block; }
</style>
</head>
<body>

<header>
  <div class="abs brand">QRV Advisors</div>
  <div class="abs questions">HAVE ANY QUESTIONS?</div>
  <svg class="abs contact-icons" width="64" height="30" viewBox="0 0 64 30" aria-label="Phone and email">
    <path d="M5 4 q-3 2 -1 9 q3 8 9 12 q4 2 6 -1 l-3 -4 q-2 1 -3 0 q-4 -4 -5 -8 q0 -2 2 -2 z" fill="none" stroke="#888" stroke-width="1.6"/>
    <path d="M14 6 q3 2 3 5 M16 3 q5 3 5 8" fill="none" stroke="#888" stroke-width="1.4"/>
    <rect x="38" y="5" width="24" height="16" fill="none" stroke="#888" stroke-width="1.6"/>
    <path d="M38 5 l12 10 l12 -10 M38 21 l9 -8 M62 21 l-9 -8" fill="none" stroke="#888" stroke-width="1.4"/>
  </svg>
  <div class="abs social-top" aria-label="Social links"><span></span><span></span><span></span><span></span><span></span></div>
</header>

<div class="abs hero"></div>
<div class="abs hero-photo" role="img" aria-label="Photo of a business person drawing connecting arrows across a world map"></div>

<nav class="abs nav">
  <a style="width:103px">THE QRV</a>
  <a style="width:121px">LOGISTICS</a>
  <a style="width:161px">MARKET ANALYSIS</a>
  <a style="width:120px">COMMUNITY</a>
  <a style="width:89px">MEDIA</a>
  <a style="width:102px">ABOUT US</a>
  <a style="width:118px">TEXAS TEAM</a>
  <a style="width:166px">CONTACT US</a>
</nav>

<section>
  <div class="abs headline-1">“QRV ADVISORS QRV</div>
  <div class="abs headline-2">A <b>LOREST</b>, NESTO <b>LACUSFEMENTINE IGIDO</b>"</div>
  <div class="abs slide-lead">Lorem ipsum dolor sit amet, consectetur adipiscing elit. Vestibulum id .</div>
  <div class="abs more-details">MORE DETAILS</div>
  <div class="abs dots"><i></i><i></i><i class="on"></i></div>
</section>

<section>
  <div class="abs card" style="left:110px">
    <h3>Drayage Calculator</h3>
    <p>Plusieurs variations de Lorem<br>Ipsum peuvent</p>
    <svg style="left:222px;top:20px" width="58" height="78" viewBox="0 0 58 78" aria-label="Ship icon">
      <rect x="26" y="2" width="4" height="10" fill="#444"/>
      <rect x="18" y="12" width="20" height="12" fill="#444"/>
      <path d="M6 26 h44 l-6 34 h-32 z" fill="#555"/>
      <path d="M28 26 v32" stroke="#fff" stroke-width="2"/>
      <path d="M2 70 q6 -6 12 0 q6 6 12 0 q6 -6 12 0 q6 6 12 0 q4 -4 6 -2" fill="none" stroke="#444" stroke-width="3"/>
    </svg>
  </div>
  <div class="abs card" style="left:458px">
    <h3 style="left:13px">Interactive Trade Map</h3>
    <p style="left:19px">Plusieurs variations de Lorem<br>Ipsum peuvent</p>
    <svg style="left:212px;top:22px" width="74" height="56" viewBox="0 0 74 56" aria-label="Folded map icon">
      <path d="M2 6 l22 -4 l24 6 l24 -6 v46 l-24 6 l-24 -6 l-22 4 z" fill="none" stroke="#555" stroke-width="3" stroke-linejoin="round"/>
      <path d="M24 2 v46 M48 8 v46" stroke="#555" stroke-width="3"/>
      <path d="M12 40 q10 -20 22 -8 q10 8 18 -10 q6 -10 12 -14" fill="none" stroke="#555" stroke-width="2" stroke-dasharray="3 3"/>
    </svg>
  </div>
  <div class="abs card" style="left:791px">
    <h3 style="left:24px">Site Plan</h3>
    <p style="left:24px">Plusieurs variations de Lorem<br>Ipsum peuvent</p>
    <svg style="left:220px;top:20px" width="64" height="66" viewBox="0 0 64 66" aria-label="Calendar icon">
      <rect x="4" y="12" width="58" height="52" rx="3" fill="none" stroke="#555" stroke-width="3"/>
      <rect x="4" y="12" width="58" height="10" fill="#555"/>
      <g fill="#555">
        <rect x="14" y="30" width="8" height="7"/><rect x="26" y="30" width="8" height="7"/><rect x="38" y="30" width="8" height="7"/><rect x="50" y="30" width="8" height="7"/>
        <rect x="14" y="41" width="8" height="7"/><rect x="26" y="41" width="8" height="7"/><rect x="38" y="41" width="8" height="7"/><rect x="50" y="41" width="8" height="7"/>
        <rect x="14" y="52" width="8" height="7"/><rect x="26" y="52" width="8" height="7"/><rect x="38" y="52" width="8" height="7"/>
      </g>
      <circle cx="16" cy="16" r="14" fill="#fff" stroke="#555" stroke-width="3"/>
      <path d="M16 8 v8 h6" fill="none" stroke="#555" stroke-width="2.5"/>
    </svg>
  </div>
</section>

<main>
  <h1 class="abs welcome-title">Welcome To QRV Advisors</h1>
  <p class="abs welcome-copy">On sait depuis longtemps que travailler avec du texte lisible et contenant du sens. est source de<br>distractions, et empêche de se concentreravec du texte lisible et contenant du sens. est source de<br>distractions, et empêche de se concentrer. sait depuis longtemps<br>que travailler avec du texte lisible et contenant du sens. est source de distractions, et empêche de se<br>concentreravec du texte lisible et contenant du sens. est source de distractions, et empêche de se</p>
  <div class="abs btn" style="left:110px;top:883px">Read More</div>

  <h2 class="abs testi-title">Testimonials</h2>
  <div class="abs avatar" style="left:829px;top:732px" role="img" aria-label="Portrait of a client"></div>
  <p class="abs quote" style="top:728px">Plusieurs variations de Lorem<br>Ipsum peuvent être trouvées<br>&nbsp;ici ou là</p>
  <div class="abs quote-name" style="left:896px;top:788px">Marlon Pierce</div>
  <div class="abs avatar" style="left:829px;top:818px" role="img" aria-label="Portrait of a client"></div>
  <p class="abs quote" style="top:818px">Plusieurs variations de Lorem<br>Ipsum peuvent être trouvées<br>&nbsp;ici ou là</p>
  <div class="abs quote-name" style="left:899px;top:879px">Marlon Pierce</div>
  <div class="abs btn" style="left:830px;top:913px">Read More</div>
</main>

<footer>
  <div class="abs footer"></div>
  <div class="abs copyright">© Copyrights 2014 All rights Reserved</div>
  <div class="abs socialize">Socialize With Us :</div>
  <div class="abs social-foot" aria-label="Social links">
    <span style="background:#2f5ea8"></span><span style="background:#1f6fa8"></span><span style="background:#3aa0dc"></span>
  </div>
</footer>

</body>
</html>
```